Fernwick Landscaping Folder Design

I need a graphic designer to design a folder so we can insert informational sheets inside it for customers. The folder must include the company logo, project images, on front and back of folder and slogan " The Experience You Want, The Service You Expect, And The Value You Deserve'

Folder to also include phone numbers : 416 555 0193 as well as the website: www.fernwicklandscaping.example as well as we gurantee a 24 month warranty.

I have attached sample of size we need.

Pixel Harbor has also done something similar for me for Tollbridge Landscapes

Target Market(s)

geared toward home owners & commercial/industrial

Industry/Entity Type

Landscaping

Font styles to use
Other font styles liked:
• open to new trendy font

Requirements
Must have
• Telephone Number, email address, slogan, images,
Nice to have
• images of completed projects incorporated into the front and back of folder as well as the logo
Should not have
• n/a

```html
<!DOCTYPE html>
<html lang="en">
<head>
<meta charset="utf-8">
<title>Fernwick Landscaping Folder</title>
<link href="https://fonts.googleapis.com/css2?family=Oswald:wght@300;600;700&family=Roboto:wght@400;700&display=swap" rel="stylesheet">
<style>
  :root {
    --backdrop: #ece9e4;
    --paper: #ffffff;
    --pocket: #58595b;
    --ink: #58595b;
    --rule: #9a9a9a;
    --slogan: #e1e1e1;
    --edge: #d8d8d8;
  }
  * { margin: 0; padding: 0; box-sizing: border-box; }
  html, body { width: 1200px; height: 1069px; overflow: hidden; }
  body { background: var(--backdrop); position: relative; font-family: "Roboto", Arial, sans-serif; }
  .folder-art { position: absolute; left: 0; top: 0; }
  .brand-name {
    position: absolute; left: 744px; top: 258px; width: 168px;
    text-align: center; font-family: "Oswald", "Arial Narrow", sans-serif;
    font-weight: 600; color: var(--ink); font-size: 26px; line-height: 30px; letter-spacing: 1.5px;
    text-transform: uppercase;
  }
  .slogan {
    position: absolute; left: 744px; top: 352px; width: 172px;
    font-family: "Oswald", "Arial Narrow", sans-serif; color: var(--slogan);
    text-transform: uppercase; letter-spacing: -0.3px; white-space: nowrap;
  }
  .slogan span { display: block; }
  .slogan .light { font-weight: 300; }
  .slogan .strong { font-weight: 700; letter-spacing: -0.6px; }
  .slogan .l1 { font-size: 29px; line-height: 31px; }
  .slogan .l2 { font-size: 38px; line-height: 33px; }
  .slogan .l3 { font-size: 37px; line-height: 36px; }
  .slogan .l4 { font-size: 34px; line-height: 32px; }
  .slogan .l5 { font-size: 31px; line-height: 31px; }
  .slogan .l6 { font-size: 32px; line-height: 31px; }
  .warranty {
    position: absolute; left: 228px; top: 642px; width: 284px;
    font-weight: 700; font-size: 14.5px; color: var(--ink); letter-spacing: 0.45px;
    padding-bottom: 5px; border-bottom: 1px solid var(--rule); white-space: nowrap;
  }
  .contact {
    position: absolute; left: 230px; top: 672px;
    font-size: 12px; color: var(--ink); display: flex; align-items: center; gap: 4px; white-space: nowrap;
  }
  .contact .dot { width: 8px; height: 8px; border-radius: 50%; background: var(--rule); display: inline-block; }
  .contact .gap { width: 2px; }
</style>
</head>
<body>
<svg class="folder-art" width="1200" height="1069" viewBox="0 0 1200 1069">
  <defs>
    <linearGradient id="g-walkway" x1="0" y1="0" x2="0.3" y2="1">
      <stop offset="0" stop-color="#5d6b3e"/><stop offset="0.35" stop-color="#7d8461"/>
      <stop offset="0.6" stop-color="#a7a49c"/><stop offset="1" stop-color="#bab6ae"/>
    </linearGradient>
    <linearGradient id="g-pool" x1="0" y1="0" x2="0.6" y2="1">
      <stop offset="0" stop-color="#4a4a30"/><stop offset="0.35" stop-color="#6a6552"/>
      <stop offset="0.6" stop-color="#2f6fc4"/><stop offset="1" stop-color="#7fb3ea"/>
    </linearGradient>
    <linearGradient id="g-garage" x1="0" y1="0" x2="0" y2="1">
      <stop offset="0" stop-color="#e9e6df"/><stop offset="0.65" stop-color="#d6d1c8"/>
      <stop offset="0.75" stop-color="#b7ab97"/><stop offset="1" stop-color="#a2957f"/>
    </linearGradient>
    <linearGradient id="g-site" x1="0" y1="0" x2="0" y2="1">
      <stop offset="0" stop-color="#cdd6df"/><stop offset="0.3" stop-color="#b7bcc2"/>
      <stop offset="0.45" stop-color="#5e6066"/><stop offset="0.6" stop-color="#8a7c6a"/>
      <stop offset="1" stop-color="#a9a69f"/>
    </linearGradient>
    <linearGradient id="g-driveway" x1="0" y1="0" x2="0" y2="1">
      <stop offset="0" stop-color="#7a6a4a"/><stop offset="0.35" stop-color="#3f4a2f"/>
      <stop offset="0.6" stop-color="#6c7250"/><stop offset="1" stop-color="#c9c7c2"/>
    </linearGradient>
  </defs>

  <rect x="143" y="127" width="456" height="813" fill="var(--paper)" stroke="var(--edge)"/>
  <rect x="600" y="127" width="457" height="813" fill="var(--paper)" stroke="var(--edge)"/>

  <rect x="152" y="137" width="437" height="168" fill="url(#g-walkway)" role="img" aria-label="Stone walkway and steps in front of a house"/>
  <rect x="152" y="306" width="218" height="157" fill="url(#g-pool)" role="img" aria-label="Backyard pool with stone waterfall"/>
  <rect x="372" y="306" width="217" height="157" fill="url(#g-garage)" role="img" aria-label="Interlocking driveway in front of garage doors"/>
  <rect x="152" y="464" width="437" height="164" fill="url(#g-site)" role="img" aria-label="Commercial concrete work at an industrial lot"/>

  <path d="M145,630 L358,566 Q372,560 386,566 L597,630 L597,737 L145,737 Z" fill="var(--paper)" stroke="var(--edge)"/>

  <path d="M603,623 L814,564 Q828,559 842,564 L1055,623" fill="none" stroke="var(--edge)" stroke-width="2"/>
  <path d="M605,626 L814,569 Q828,564 842,569 L1053,626 L1053,737 L605,737 Z" fill="url(#g-driveway)" role="img" aria-label="Curved concrete driveway leading to a house"/>

  <rect x="143" y="737" width="456" height="203" fill="var(--pocket)"/>
  <rect x="600" y="737" width="457" height="203" fill="var(--pocket)"/>
  <line x1="599.5" y1="127" x2="599.5" y2="940" stroke="var(--edge)"/>
</svg>

<div class="brand-name">Fernwick<br>Landscaping</div>

<div class="slogan">
  <span class="light l1">The Experience</span>
  <span class="strong l2">You Want,</span>
  <span class="light l3">The Service</span>
  <span class="strong l4">You Expect,</span>
  <span class="light l5">And The Value</span>
  <span class="strong l6">You Deserve</span>
</div>

<div class="warranty">WE GURANTEE A 24 MONTH WARRANTY</div>
<div class="contact">
  <span class="dot"></span><span>416 555 0193</span><span class="gap"></span>
  <span class="dot"></span><span>www.fernwicklandscaping.example</span>
</div>
</body>
</html>
```